business card deign

Logo needs the following on it.
1. attached logo
2. Tagline - "If it keeps a drink cold or the party going...we do it!"
3. Name- Dalton Pikes, Founder and CPO
4. Address - 412 E. Carver Avenue, Ste 2207, Tampa, FL. 33917
5. Phone - 555.318.4726

```html
<!DOCTYPE html>
<html lang="en">
<head>
<meta charset="utf-8">
<title>Kelvara Business Card</title>
<link href="https://fonts.googleapis.com/css2?family=Courgette&family=Lato:wght@300;400;900&display=swap" rel="stylesheet">
<style>
  :root {
    --bg: #3a3a3a;
    --card-dark: #000000;
    --card-light: #ffffff;
    --ink: #111111;
    --ink-soft: #555555;
    --rule: #8a8a8a;
    --art-tone: #d9d9d9;
    --art-tone-dark: #e8e8e8;
  }
  * { margin: 0; padding: 0; box-sizing: border-box; }
  html, body { width: 1200px; height: 875px; overflow: hidden; }
  body {
    background: var(--bg);
    font-family: "Lato", sans-serif;
    position: relative;
  }
  .card {
    position: absolute;
    width: 580px;
    height: 330px;
    border-radius: 22px;
    overflow: hidden;
  }
  /* Back side */
  .card-back {
    left: 60px;
    top: 70px;
    background: var(--card-dark);
  }
  .card-back .mascot-art {
    position: absolute;
    left: 215px;
    top: 34px;
    width: 150px;
    height: 200px;
    border-radius: 12px;
    background: linear-gradient(180deg, var(--art-tone-dark), #bdbdbd);
  }
  .card-back .tagline {
    position: absolute;
    left: 0;
    right: 0;
    top: 262px;
    text-align: center;
    color: var(--card-light);
    font-family: "Courgette", cursive;
    font-size: 21px;
  }
  /* Front side */
  .card-front {
    left: 560px;
    top: 475px;
    background: var(--card-light);
  }
  .brand {
    position: absolute;
    right: 40px;
    top: 118px;
    font-family: "Lato", sans-serif;
    font-weight: 900;
    font-size: 26px;
    letter-spacing: 14px;
    color: var(--ink);
  }
  .divider {
    position: absolute;
    left: 40px;
    right: 40px;
    top: 168px;
    height: 1px;
    background: var(--ink);
  }
  .address {
    position: absolute;
    right: 40px;
    top: 180px;
    text-align: right;
    font-size: 15px;
    line-height: 1.35;
    color: var(--ink-soft);
  }
  .person {
    position: absolute;
    left: 40px;
    top: 132px;
  }
  .person .name {
    font-weight: 900;
    font-size: 29px;
    color: var(--ink);
    text-transform: uppercase;
    letter-spacing: 0.5px;
  }
  .person .role {
    margin-top: 10px;
    font-size: 17px;
    color: var(--ink-soft);
  }
  .person .short-rule {
    margin-top: 12px;
    width: 200px;
    height: 1px;
    background: var(--rule);
  }
  .contacts {
    list-style: none;
    position: absolute;
    left: 40px;
    top: 246px;
    font-size: 15px;
    color: var(--ink-soft);
  }
  .contacts li {
    display: flex;
    align-items: center;
    gap: 10px;
    height: 22px;
  }
  .contacts svg { width: 13px; height: 13px; fill: var(--ink); }
</style>
</head>
<body>
  <section class="card card-back">
    <div class="mascot-art" role="img" aria-label="White silhouette illustration of the brand mascot"></div>
    <p class="tagline">If it keeps a drink cold or the party going...we do it!</p>
  </section>

  <section class="card card-front">
    <div class="brand">KELVARA</div>
    <div class="divider"></div>
    <address class="address">
      412 E. Carver Avenue<br>
      Ste 2207<br>
      Tampa, FL 33917
    </address>
    <div class="person">
      <h1 class="name">Dalton Pikes</h1>
      <p class="role">Founder &amp; CEO</p>
      <div class="short-rule"></div>
    </div>
    <ul class="contacts">
      <li>
        <svg viewBox="0 0 16 16" aria-hidden="true"><circle cx="8" cy="8" r="8"/><path d="M5 4l2 2-1 1a5 5 0 003 3l1-1 2 2-1 1.5C8 12 4 8 3.5 5z" fill="#fff"/></svg>
        555.318.4726
      </li>
      <li>
        <svg viewBox="0 0 16 16" aria-hidden="true"><rect x="1" y="3" width="14" height="10"/><path d="M1.5 3.5L8 9l6.5-5.5" stroke="#fff" stroke-width="1.4" fill="none"/></svg>
        dalton@kelvara.com
      </li>
      <li>
        <svg viewBox="0 0 16 16" aria-hidden="true"><circle cx="8" cy="8" r="8"/><path d="M1 8h14M8 1c-3 3-3 11 0 14M8 1c3 3 3 11 0 14" stroke="#fff" stroke-width="1.2" fill="none"/></svg>
        www.kelvara.com
      </li>
    </ul>
  </section>
</body>
</html>
```